Home Security Company Business Card

Looking for a eye catching business card that is non traditional and stands out but yet still looks professional. It should include all the pertinent information such as name, title, address, telephone, e-mail, website address should definitely stand out and then finally the logo.

Target Market(s)

Residential and Commercial accounts mostly upscale accounts

Industry/Entity Type

Security

Contact Information for Business Card

Name
Title
Address
Office #
Cell #
E-mail
Website

Font styles to use
Serif
Sans Serif

Requirements
Must have
• Logo, two sided color configuration
Nice to have
• You decide
Should not have
• There really aren't any.

```html
<!DOCTYPE html>
<html lang="en">
<head>
<meta charset="utf-8">
<title>Ironvale Protection Group – Business Card</title>
<link rel="stylesheet" href="https://fonts.googleapis.com/css2?family=Open+Sans:wght@400;600;700&family=Cinzel:wght@600&display=swap">
<style>
  :root {
    --stage: #e9e6e1;
    --gold: #eec04e;
    --paper: #ffffff;
    --maroon: #7a1616;
    --muted: #a8632a;
    --rule: #b88a3a;
    --shadow: rgba(0,0,0,0.35);
  }
  * { box-sizing: border-box; margin: 0; padding: 0; }
  html, body { width: 1200px; height: 750px; overflow: hidden; }
  body {
    background: var(--stage);
    position: relative;
    font-family: "Open Sans", Arial, sans-serif;
    color: var(--maroon);
  }
  .card {
    position: absolute;
    top: 200px;
    height: 320px;
    border-radius: 18px;
    box-shadow: 0 6px 14px var(--shadow);
    overflow: hidden;
  }
  .card--front { left: 28px; width: 559px; background: var(--gold); }
  .card--back { left: 614px; width: 558px; background: var(--paper); }

  .brand {
    font-family: "Cinzel", Georgia, serif;
    font-weight: 600;
    color: var(--maroon);
    line-height: 1.15;
    letter-spacing: 0.5px;
  }
  .brand__mark {
    display: inline-block;
    background: var(--maroon);
    vertical-align: middle;
  }
  .card--front .brand {
    position: absolute;
    left: 42px; top: 56px;
    font-size: 15px;
    display: flex; align-items: center; gap: 10px;
  }
  .card--front .brand__mark { width: 14px; height: 14px; }

  .holder { position: absolute; left: 42px; top: 160px; width: 420px; }
  .holder__name { font-size: 23px; font-weight: 700; line-height: 1.2; }
  .holder__title {
    font-size: 15px; color: var(--muted);
    border-bottom: 1px solid var(--rule);
    padding-bottom: 1px; line-height: 1.3;
  }

  .contacts { position: absolute; left: 42px; top: 216px; list-style: none; }
  .contacts li {
    font-size: 15.5px; line-height: 19.5px;
    display: flex; align-items: center; gap: 8px;
  }
  .contacts svg { width: 13px; height: 13px; fill: var(--maroon); flex: none; }

  .card--back .brand {
    position: absolute;
    left: 0; right: 0; top: 110px;
    text-align: center;
    font-size: 28px;
    display: flex; justify-content: center; align-items: center; gap: 14px;
  }
  .card--back .brand__mark { width: 22px; height: 22px; }
  .website {
    position: absolute; left: 0; right: 0; top: 254px;
    text-align: center;
    font-size: 15.5px; font-weight: 700;
  }
</style>
</head>
<body>
  <section class="card card--front" aria-label="Business card front">
    <div class="brand"><span class="brand__mark"></span><span>Ironvale<br>Protection Group</span></div>
    <div class="holder">
      <p class="holder__name">Daniel Marlowe</p>
      <p class="holder__title">Owner</p>
    </div>
    <ul class="contacts">
      <li><svg viewBox="0 0 16 16" aria-hidden="true"><path d="M1 6c0-2 3-3.5 7-3.5S15 4 15 6v1.5h-3.5V6h-7v1.5H1zM3 9h10l1 5H2z"/></svg>+330 5550-1234</li>
      <li><svg viewBox="0 0 16 16" aria-hidden="true"><path d="M3 1h3l1 4-2 1.5c1 2 2.5 3.5 4.5 4.5L11 9l4 1v3c0 1-1 2-2 2C7 15 1 9 1 3c0-1 1-2 2-2z"/></svg>+3305550-48210</li>
      <li><svg viewBox="0 0 16 16" aria-hidden="true"><path d="M1 3h14v10H1zm1.5 1.5v.3L8 9l5.5-4.2v-.3zm0 2.2v4.8h11V6.7L8 11z"/></svg>info@danielmarlowemail.com</li>
      <li><svg viewBox="0 0 16 16" aria-hidden="true"><path d="M8 0a5.5 5.5 0 0 1 5.5 5.5C13.5 10 8 16 8 16S2.5 10 2.5 5.5A5.5 5.5 0 0 1 8 0zm0 3.3a2.2 2.2 0 1 0 0 4.4 2.2 2.2 0 0 0 0-4.4z"/></svg>220 Harbor Lane Westbrook, Ohio 44100</li>
    </ul>
  </section>

  <section class="card card--back" aria-label="Business card back">
    <div class="brand"><span class="brand__mark"></span><span>Ironvale<br>Protection Group</span></div>
    <p class="website">www.ironvaleprotectiongroup.com</p>
  </section>
</body>
</html>
```